Small corporate website template design

I need a couple templates designed for a small corporate website. The corporate site reflects the existence of the parent company which will own various brands/services that have their own websites, so it will mainly be used to present who we are, what we do, what is happening (news/events), how to contact us, link off to our other brand/service sites, as well as post information for public relations, investors, and job opportunities.

The company name is Brelvanto LLC (www.brelvanto-example.com), and the name is representative of stratified layers of interconnected digital services. The corporate site is not expected to generate a bunch of fanfare - that honor will be reserved for the externally linked brand/service sites.

The provided logo may be manipulated in color, size, shape, positioning, etc. to get it to fit with the design, but should be integrated in some way.

What we are looking for is a home page layout as well as a template for an inner page whereby the navigation/logo, etc may be diminished to some extent for the inner pages. We are also interested in reusable elements such as dividers, content containers, etc. in order to represent the types of information described above that we would like to present as described above.

We are particularly interested in consistency of design elements, conservative use of color (including consideration of accessibility concerns), judicious use of whitespace in favor of simplified messaging, and something lending itself well to internationalization/translation.

Target Market(s)

Small business owners, entrepreneurs (B2B)

Number of Pages Required

2 page

Font styles to use
Sans Serif

Requirements
Must have
• See the attached PDF with the logo concept, color swatches, and comparative sites.

```html
<!DOCTYPE html>
<html lang="en">
<head>
<meta charset="utf-8">
<title>Brelvanto LLC</title>
<link rel="stylesheet" href="https://fonts.googleapis.com/css2?family=Montserrat:wght@400;600;700&family=Open+Sans:wght@400;600&display=swap">
<style>
  :root{
    --blue:#1d63b5;
    --navy:#0c2d63;
    --ink:#1e2a3a;
    --grey:#6d7580;
    --green:#7dc11f;
    --green-dark:#5e9a12;
    --orange:#f7941d;
    --paper:#ffffff;
    --mist:#eef1f5;
  }
  *{box-sizing:border-box;margin:0;padding:0}
  html,body{width:733px;height:1200px;overflow:hidden;background:var(--paper)}
  body{font-family:"Open Sans",Arial,sans-serif;color:var(--ink)}
  .page{position:relative;width:733px;height:1200px;overflow:hidden;background:var(--paper)}
  .abs{position:absolute}

  /* header */
  .hero-backdrop{left:0;top:0;width:733px;height:430px;background:radial-gradient(ellipse at 30% 40%,#ffffff 0%,#f1f3f6 70%,#e6e9ee 100%)}
  .brand{left:73px;top:18px;display:flex;align-items:center;gap:8px;font-family:"Montserrat",Arial,sans-serif;font-weight:600;font-size:20px;color:var(--ink)}
  .brand-dot{width:28px;height:28px;border-radius:50%;background:var(--ink)}
  .nav{left:264px;top:31px;display:flex;gap:18px;font-family:"Montserrat",Arial,sans-serif;font-size:9px;font-weight:600;color:var(--grey);text-transform:uppercase;letter-spacing:.3px}
  .nav .active{color:var(--ink)}

  .hero-title{left:73px;top:152px;font-family:"Montserrat",Arial,sans-serif;font-weight:700;font-size:22px;line-height:25px;color:var(--ink);text-transform:uppercase}
  .hero-title .accent{color:var(--blue)}
  .btn{display:inline-block;font-family:"Montserrat",Arial,sans-serif;font-weight:600;font-size:10px;color:#fff;border-radius:14px;text-align:center}
  .btn-green{left:73px;top:250px;width:86px;height:28px;line-height:28px;background:var(--green)}
  .hero-visual{left:390px;top:60px;width:306px;height:300px}
  .slider-dots{left:476px;top:352px;display:flex;gap:5px}
  .slider-dots span{width:6px;height:6px;border-radius:50%;background:#b9c0c9}
  .slider-dots span.on{background:var(--ink)}

  /* who we are */
  .who-band{left:0;top:360px;width:733px;height:350px}
  .who{left:0;top:462px;width:733px;text-align:center;color:#fff}
  .section-title{font-family:"Montserrat",Arial,sans-serif;font-weight:600;font-size:20px;letter-spacing:.5px;text-transform:uppercase}
  .who p{width:470px;margin:10px auto 0;font-size:8.5px;line-height:13px;color:#d6e2f2}
  .btn-outline{margin-top:18px;width:86px;height:25px;line-height:23px;border:1.5px solid #fff;background:transparent}

  /* contact */
  .contact-backdrop{left:0;top:700px;width:733px;height:320px;background:linear-gradient(90deg,#ffffff 0%,#f4f5f7 60%,#eceef1 100%)}
  .contact-visual{left:61px;top:708px;width:281px;height:282px;border-radius:4px;background:linear-gradient(135deg,#f3f3f3 0%,#c9ccd1 55%,#9aa0a8 100%)}
  .contact{left:374px;top:748px;width:300px}
  .contact .section-title{color:var(--ink);font-size:19px}
  .contact p{margin-top:6px;font-size:8px;line-height:12px;color:var(--grey);width:250px}
  .contact-list{list-style:none;margin-top:12px}
  .contact-list li{display:flex;align-items:center;gap:10px;height:30px;font-size:9px;color:var(--ink)}
  .contact-list svg{width:20px;height:20px}
  .btn-orange{margin-top:12px;width:92px;height:24px;line-height:24px;border-radius:3px;background:var(--orange)}

  /* footer */
  .footer-band{left:0;top:995px;width:733px;height:205px}
  .footer-mark{left:96px;top:1030px;width:46px;height:46px;border-radius:50%;background:rgba(255,255,255,.35)}
  .social{left:86px;top:1104px;display:flex;gap:6px}
  .social span{width:15px;height:15px;border-radius:50%;border:1.5px solid #fff}
  .footer-col{top:1030px;color:#fff}
  .footer-col h4{font-family:"Montserrat",Arial,sans-serif;font-size:10px;font-weight:700;text-transform:uppercase;margin-bottom:8px}
  .footer-col ul{list-style:none;font-size:8.5px;line-height:15px}
  .col-links{left:225px}
  .col-res{left:354px}
  .col-blog{left:476px;width:200px}
  .col-blog li{display:flex;gap:6px;line-height:11px;margin-bottom:6px}
  .col-blog li::before{content:"";flex:none;width:4px;height:4px;margin-top:4px;border-radius:50%;background:#fff}
  .copyright{left:0;top:1160px;width:733px;height:40px;line-height:40px;text-align:center;font-size:8px;color:#eaf6d6;background:var(--green-dark)}
</style>
</head>
<body>
<div class="page">

  <div class="abs hero-backdrop"></div>

  <header>
    <div class="abs brand"><span class="brand-dot"></span>Brelvanto</div>
    <nav class="abs nav">
      <span class="active">Home</span><span>About Us</span><span>Who We Are</span><span>What We Do</span><span>News</span><span>Jobs</span><span>Contact</span>
    </nav>
  </header>

  <section class="hero">
    <h1 class="abs hero-title"><span class="accent">Adaptive Software</span><br>Technology for<br>the Digital Revolution</h1>
    <a class="abs btn btn-green">Learn More</a>
    <svg class="abs hero-visual" viewBox="0 0 306 300" role="img" aria-label="Photo of a hand touching a glowing blue digital network, framed in a hexagon">
      <defs>
        <radialGradient id="heroGlow" cx="55%" cy="45%" r="65%">
          <stop offset="0" stop-color="#bfe3ff"/>
          <stop offset=".35" stop-color="#2a7fd0"/>
          <stop offset="1" stop-color="#0a1f4a"/>
        </radialGradient>
      </defs>
      <polygon points="76,0 230,0 306,150 230,300 76,300 0,150" fill="#d9dee6"/>
      <polygon points="82,10 224,10 295,150 224,290 82,290 11,150" fill="url(#heroGlow)"/>
    </svg>
    <div class="abs slider-dots"><span class="on"></span><span></span><span></span><span></span></div>
  </section>

  <svg class="abs who-band" viewBox="0 0 733 350" preserveAspectRatio="none" aria-hidden="true">
    <defs>
      <linearGradient id="whoFill" x1="0" y1="0" x2="1" y2="1">
        <stop offset="0" stop-color="#1d5aa8"/>
        <stop offset="1" stop-color="#0a2452"/>
      </linearGradient>
    </defs>
    <polygon points="0,55 733,10 733,330 0,340" fill="url(#whoFill)"/>
  </svg>
  <section class="abs who">
    <h2 class="section-title">Who We Are</h2>
    <p>Magna nisi nisl, elit vestibulum placerat at tellus nec, ultricies sit amet porttitor mattis enim in massa. Morbi interdum nisi, blandit vel congue ut, ullamcorper nec eget tempor cursus mauris. Praesent suscipit velit cursus at tellus nec sed lobortis facilisis lorem blandit dictum eget.</p>
    <a class="btn btn-outline">Learn More</a>
  </section>

  <div class="abs contact-backdrop"></div>
  <div class="abs contact-visual" role="img" aria-label="Top-down photo of a laptop, glasses, a small plant and a coffee cup on a white desk"></div>
  <section class="abs contact">
    <h2 class="section-title">Contact Us</h2>
    <p>Pellentesque faucibus id accumsan ultrices sit amet nisl, maecenas sagittis in velit pulvinar sodales dolor lorem.</p>
    <ul class="contact-list">
      <li>
        <svg viewBox="0 0 20 20" aria-hidden="true"><circle cx="10" cy="10" r="10" fill="var(--blue)"/><path d="M10 4.5a3.5 3.5 0 0 0-3.5 3.5c0 2.6 3.5 7 3.5 7s3.5-4.4 3.5-7A3.5 3.5 0 0 0 10 4.5zm0 4.8a1.3 1.3 0 1 1 0-2.6 1.3 1.3 0 0 1 0 2.6z" fill="#fff"/></svg>
        482 Larkmoor Avenue, Dalby, TX 75990
      </li>
      <li>
        <svg viewBox="0 0 20 20" aria-hidden="true"><circle cx="10" cy="10" r="10" fill="var(--blue)"/><path d="M7.2 5.5l1.6 0 .8 2.3-1.1.9a6 6 0 0 0 2.8 2.8l.9-1.1 2.3.8v1.6c0 .6-.5 1-1.1 1A8.3 8.3 0 0 1 6.2 6.6c0-.6.4-1.1 1-1.1z" fill="#fff"/></svg>
        555.014.2290
      </li>
      <li>
        <svg viewBox="0 0 20 20" aria-hidden="true"><circle cx="10" cy="10" r="10" fill="var(--blue)"/><rect x="5" y="6.5" width="10" height="7" rx="1" fill="#fff"/><path d="M5.3 7l4.7 3.6L14.7 7" fill="none" stroke="var(--blue)" stroke-width="1"/></svg>
        hello@brelvanto-example.com
      </li>
    </ul>
    <a class="btn btn-orange">Contact Us Now</a>
  </section>

  <svg class="abs footer-band" viewBox="0 0 733 205" preserveAspectRatio="none" aria-hidden="true">
    <polygon points="0,10 733,25 733,205 0,205" fill="var(--green)"/>
  </svg>
  <footer>
    <div class="abs footer-mark" aria-hidden="true"></div>
    <div class="abs social" aria-hidden="true"><span></span><span></span><span></span><span></span><span></span></div>
    <div class="abs footer-col col-links">
      <h4>Quick Links</h4>
      <ul><li>About Us</li><li>What We Do</li><li>Who We Are</li><li>Why Us</li></ul>
    </div>
    <div class="abs footer-col col-res">
      <h4>Resources</h4>
      <ul><li>News &amp; Blogs</li><li>Team</li><li>Contact Us</li></ul>
    </div>
    <div class="abs footer-col col-blog">
      <h4>Our Blogs</h4>
      <ul>
        <li>Short news from our team this month</li>
        <li>Notes on building shared digital services</li>
        <li>Welcoming new brands into our family of sites</li>
      </ul>
    </div>
    <div class="abs copyright">© 2024 Brelvanto LLC. All rights reserved.</div>
  </footer>

</div>
</body>
</html>
```